New Business Card Design Project

We require a business card design for Vexalund, a newly established Indian company.
Our focus is on the development, manufacturing, and export of a diverse array of pharmaceutical products on a global scale. The card should convey a professional appearance, as our primary markets are in Africa, China, and Southeast Asian nations.
We envision a two-sided business card, with the reverse side dedicated to a logo set against a solid color or an elegantly designed pattern. The corners should be rounded. We would appreciate seeing both horizontal and vertical design options. We trust the designer to utilize their expertise in creating this design.

The content for the business card is included in the attached Word file.

Target Market(s)

Our primary markets are in Africa, China, and Southeast Asian, Latin America, Maldives, Sri Lanka

Industry/Entity Type

Pharmaceutical Manufacturing and Export

Contact Information for Business Card

Colors

Designer to choose colors to be used in the design.

Requirements
Must have
• The reverse side of the business card features solely the logo along with the tagline, "Care for Every Life."
Should not have
• The logo should not exceed two instances, encompassing both the front and back sides of the card.

```html
<!DOCTYPE html>
<html lang="en">
<head>
<meta charset="utf-8">
<title>Vexalund – Business Card</title>
<link rel="stylesheet" href="https://fonts.googleapis.com/css2?family=Open+Sans:wght@400;600;700&family=Poppins:wght@400;700&display=swap">
<style>
  :root {
    --stage: #2a2a2c;
    --card: #222226;
    --blue: #2ca6df;
    --coral: #f0634f;
    --white: #ffffff;
    --brand-font: "Poppins", sans-serif;
    --body-font: "Open Sans", sans-serif;
  }
  * { box-sizing: border-box; margin: 0; padding: 0; }
  html, body { width: 1200px; height: 711px; overflow: hidden; }
  body { background: var(--stage); position: relative; font-family: var(--body-font); }

  .card {
    position: absolute;
    top: 200px;
    width: 540px;
    height: 310px;
    background: var(--card);
    border-radius: 22px;
    border-bottom: 3px solid var(--blue);
    border-left: 3px solid var(--blue);
    overflow: hidden;
    box-shadow: 0 14px 30px rgba(0,0,0,0.55);
  }
  .card--back { left: 40px; }
  .card--front { left: 620px; }

  /* Back side */
  .back-brand {
    position: absolute;
    left: 0; right: 0; top: 108px;
    display: flex; align-items: center; justify-content: center; gap: 14px;
  }
  .brand-dot {
    width: 26px; height: 26px; border-radius: 50%;
    background: var(--coral);
    flex: none;
  }
  .brand-name {
    font-family: var(--brand-font);
    font-weight: 700;
    color: var(--blue);
    font-size: 58px;
    line-height: 1;
    letter-spacing: -0.5px;
    white-space: nowrap;
  }
  .tagline {
    position: absolute;
    left: 0; right: 0; top: 205px;
    text-align: center;
    font-family: var(--brand-font);
    font-size: 15px;
    color: var(--blue);
    letter-spacing: 0.5px;
  }

  /* Front side */
  .front-brand {
    position: absolute;
    left: 30px; top: 112px;
    display: flex; align-items: center; gap: 10px;
  }
  .front-brand .brand-name { font-size: 44px; }
  .front-brand .brand-dot { width: 20px; height: 20px; }

  .divider {
    position: absolute;
    left: 290px; top: 40px;
    width: 1px; height: 190px;
    background: var(--blue);
    opacity: 0.8;
  }

  .person {
    position: absolute;
    left: 318px; top: 56px;
  }
  .person-name { font-size: 23px; line-height: 1.1; white-space: nowrap; }
  .person-first { font-weight: 700; color: var(--blue); }
  .person-last { font-weight: 400; color: var(--coral); }
  .person-role { color: var(--white); font-size: 14px; margin-top: 2px; }

  .contacts {
    position: absolute;
    left: 318px; top: 128px;
    list-style: none;
  }
  .contacts li {
    display: flex; align-items: center; gap: 10px;
    color: var(--white);
    font-size: 13px;
    margin-bottom: 8px;
    white-space: nowrap;
  }
  .contacts svg { width: 15px; height: 15px; flex: none; }

  .address-band {
    position: absolute;
    left: 0; bottom: 18px;
    width: 440px; height: 28px;
    background: var(--blue);
    color: var(--white);
    font-size: 13px;
    display: flex; align-items: center; justify-content: flex-end;
    padding-right: 22px;
    white-space: nowrap;
  }
  .accent-band {
    position: absolute;
    right: 0; bottom: 46px;
    width: 100px; height: 28px;
    background: var(--coral);
  }
</style>
</head>
<body>

  <section class="card card--back" aria-label="Card back">
    <div class="back-brand">
      <span class="brand-dot"></span>
      <span class="brand-name">Vexalund</span>
    </div>
    <p class="tagline">Care for Every Life.</p>
  </section>

  <section class="card card--front" aria-label="Card front">
    <div class="front-brand">
      <span class="brand-dot"></span>
      <span class="brand-name">Vexalund</span>
    </div>

    <div class="divider"></div>

    <div class="person">
      <p class="person-name"><span class="person-first">Rohan</span> <span class="person-last">K. Sathe</span></p>
      <p class="person-role">CEO</p>
    </div>

    <ul class="contacts">
      <li>
        <svg viewBox="0 0 16 16" aria-hidden="true"><rect x="4" y="1.5" width="8" height="13" rx="1.5" fill="none" stroke="#f0634f" stroke-width="1.6"/></svg>
        +91 98230 51746
      </li>
      <li>
        <svg viewBox="0 0 16 16" aria-hidden="true"><circle cx="8" cy="8" r="6.5" fill="none" stroke="#2ca6df" stroke-width="1.5"/><ellipse cx="8" cy="8" rx="2.8" ry="6.5" fill="none" stroke="#2ca6df" stroke-width="1.2"/><line x1="1.5" y1="8" x2="14.5" y2="8" stroke="#2ca6df" stroke-width="1.2"/></svg>
        www.vexalund.com
      </li>
      <li>
        <svg viewBox="0 0 16 16" aria-hidden="true"><rect x="1.5" y="3.5" width="13" height="9" rx="1" fill="none" stroke="#f0634f" stroke-width="1.5"/><polyline points="1.5,4 8,9 14.5,4" fill="none" stroke="#f0634f" stroke-width="1.5"/></svg>
        rsathe@vexalund.com
      </li>
    </ul>

    <div class="accent-band"></div>
    <div class="address-band">12, Lotus Park Road, Nagpur, 440010, India</div>
  </section>

</body>
</html>
```